Forensic Document Examiner, looking for contemporary update to my stationery design.

Looking for professional, classy logo design for stationery and business cards. My current stationery and business card is attached.I believe a logo image makes a header section interesting, so an intriguing design of a pen, feathered pen, microscope, magnifying glass, etc., would be appropriate. I have been in the business for over 30 years. I leave ideas to the imagination of the designer.My work involves mainly, the comparison of signatures and handwriting. I also resolve alterations, obliterations, and work as shown on my website: www.documentexaminer.infoThe image produced will be printed on quality white stationery and envelopes. The stationery will be photocopied by my clients, so the images should be reproducible. The business cards may be designed in other than white.

Target Market(s)

Attorneys

Font styles to use
Sans Serif

Colors

Designer to choose colors to be used in the design.

Requirements
Must have
• Image suitable for white stationery and photocopying.
• Classy logo and image; no casual fonts.
Nice to have
• Intriguing, contemporary design incorporating a relevant logo to my work.

```html
<!DOCTYPE html>
<html lang="en">
<head>
<meta charset="utf-8">
<title>Martin B. Hale — Envelope Stationery</title>
<link rel="stylesheet" href="https://fonts.googleapis.com/css2?family=Libre+Baskerville:ital,wght@0,400;0,700;1,400&display=swap">
<style>
  :root {
    --backdrop: #a8a8a8;
    --paper: #f2f2f2;
    --paper-shade: #e6e6e6;
    --navy: #2f2b7a;
    --ink-grey: #8c8c8c;
    --flap-grey: #bdbdbd;
    --flap-line: #d2d2d2;
  }
  html, body {
    margin: 0;
    width: 1200px;
    height: 950px;
    overflow: hidden;
    background: var(--backdrop);
  }
  .canvas {
    position: relative;
    width: 1200px;
    height: 950px;
    font-family: "Libre Baskerville", Georgia, serif;
  }
  .envelope {
    position: absolute;
    width: 560px;
    height: 270px;
    background: var(--paper);
    box-shadow: 0 6px 18px rgba(0,0,0,0.18);
  }
  .envelope--front { left: 60px; top: 110px; }
  .envelope--back { left: 580px; top: 560px; background: var(--paper-shade); }

  .edge-rule {
    position: absolute;
    left: 0;
    top: 128px;
    width: 26px;
    height: 2px;
    background: var(--navy);
  }
  .bottom-band {
    position: absolute;
    left: 240px;
    bottom: 0;
    width: 120px;
    height: 6px;
    background: var(--navy);
  }
  .sender {
    position: absolute;
    left: 40px;
    top: 58px;
  }
  .sender__name {
    display: flex;
    align-items: center;
    gap: 8px;
    margin: 0;
    font-size: 20px;
    font-weight: 700;
    color: var(--navy);
    letter-spacing: 0.2px;
  }
  .sender__mark {
    width: 9px;
    height: 9px;
    background: var(--navy);
  }
  .sender__title {
    margin: 4px 0 0;
    padding-bottom: 4px;
    border-bottom: 1px solid var(--ink-grey);
    width: 220px;
    font-size: 11px;
    font-style: italic;
    color: var(--ink-grey);
  }
  .sender__address {
    margin: 4px 0 0;
    font-size: 10.5px;
    font-style: italic;
    color: var(--navy);
  }

  .flap {
    position: absolute;
    left: 580px;
    top: 450px;
    width: 560px;
    height: 110px;
  }
  .flap svg { display: block; }

  .back-name {
    position: absolute;
    right: 90px;
    bottom: 70px;
    display: flex;
    align-items: center;
    gap: 6px;
    font-size: 14px;
    font-weight: 700;
    color: var(--navy);
  }
  .back-name__dot {
    width: 8px;
    height: 8px;
    border-radius: 50%;
    background: var(--navy);
  }
  .inner-pocket {
    position: absolute;
    left: 14px;
    top: 14px;
    right: 14px;
    bottom: 0;
    border: 1px solid #dcdcdc;
    border-bottom: none;
    border-radius: 14px 14px 0 0;
  }
</style>
</head>
<body>
<main class="canvas">

  <section class="envelope envelope--front" aria-label="Envelope front">
    <span class="edge-rule"></span>
    <div class="sender">
      <p class="sender__name">Martin B. Hale <span class="sender__mark"></span></p>
      <p class="sender__title">Forensic Document Examiner</p>
      <p class="sender__address">1187 Alder Ridge Rd Salem OR 97302</p>
    </div>
    <span class="bottom-band"></span>
  </section>

  <div class="flap">
    <svg width="560" height="110" viewBox="0 0 560 110" role="img" aria-label="Inner flap with grey interlocking geometric pattern">
      <path d="M0 110 L0 30 Q0 0 30 0 L530 0 Q560 0 560 30 L560 110 Z" fill="var(--flap-grey)"/>
    </svg>
  </div>

  <section class="envelope envelope--back" aria-label="Envelope back">
    <span class="inner-pocket"></span>
    <div class="back-name"><span class="back-name__dot"></span>Martin B. Hale</div>
  </section>

</main>
</body>
</html>
```